Elegant, High End Integrated Wellness Healthcare Practice

We need a brochure designed for an integrated mind-body wellness healthcare practice (www.quellarivecare.com) . This brochure will be used when we cold call prospects (physicians to refer to our office, and potential consumers to utilize our services). Our practice is geographically located in the middle Tennessee USA region, although we have plans to become an international company as many of our offerings can be accessed anywhere in the world. Ultimately our goal is to have this brochure used as a leave-behind in an effort to introduce our integrated offerings to increase market share. The final product brochure should be both elegant and serious, with clean lines but also convey warmth and trust, as individuals who are coming for our services have usually struggled with their health for a significant amount of time before finding our practice.
Updates

The design brief was very specific about providing a high-end science-based 2-page brochure (not flier). Several designs submitted were fliers. The other designs were heavy on yoga or "woo woo" non-science-based looking pictures. This is a flier to appeal to physicians and other healthcare providers. Therefore the design must speak science and evidence-based methods of mind and body wellness care. I would also like to appeal to the other designers I paid extra for their submissions and who have indicated they will "respond in the coming days."

```html
<!DOCTYPE html>
<html lang="en">
<head>
<meta charset="utf-8">
<title>Quellarive Care – Brochure</title>
<link rel="stylesheet" href="https://fonts.googleapis.com/css2?family=Poppins:wght@300;400;600;700&family=Lato:wght@400&display=swap">
<style>
  :root {
    --green: #7ab03a;
    --green-light: #8cc43f;
    --green-mid: #5d9128;
    --green-dark: #243a0a;
    --green-deep: #1c3008;
    --night: #07212a;
    --ink: #111111;
    --paper: #ffffff;
    --canvas: #ffffff;
  }
  * { box-sizing: border-box; margin: 0; padding: 0; }
  html, body { width: 1200px; height: 780px; overflow: hidden; background: var(--canvas); }
  body { position: relative; font-family: "Poppins", sans-serif; color: var(--ink); }

  .page {
    position: absolute; top: 15px; width: 576px; height: 745px;
    background: var(--paper); overflow: hidden;
    box-shadow: 0 0 3px rgba(0,0,0,0.18);
  }
  .page--cover { left: 15px; }
  .page--values { left: 608px; }
  .page__art { position: absolute; inset: 0; width: 100%; height: 100%; }

  /* Cover */
  .brand { position: absolute; left: 29px; top: 515px; display: flex; align-items: center; gap: 14px; }
  .brand__ring { width: 98px; height: 98px; border-radius: 50%; border: 7px solid var(--green-dark); flex: none; }
  .brand__name {
    font-family: "Poppins", sans-serif; font-weight: 600; color: var(--green-dark);
    font-size: 38px; line-height: 50px; text-transform: uppercase; letter-spacing: 1px;
  }
  .tagline {
    position: absolute; left: 29px; top: 644px;
    font-weight: 300; font-size: 17.5px; line-height: 33px; color: var(--green);
    letter-spacing: 0.4px; text-transform: uppercase;
  }

  /* Values page */
  .values__title {
    position: absolute; left: 0; right: 0; top: 24px; text-align: center;
    font-weight: 700; font-size: 25px; letter-spacing: 0.5px;
  }
  .values__subtitle {
    position: absolute; left: 0; right: 0; top: 62px; text-align: center;
    font-weight: 300; font-size: 24px; letter-spacing: 0.6px;
  }
  .value { position: absolute; left: 102px; width: 428px; }
  .value__heading { font-weight: 600; font-size: 13px; line-height: 18px; }
  .value__lead { font-weight: 400; font-size: 8.6px; line-height: 14px; margin-top: 3px; }
  .value__body {
    font-family: "Lato", sans-serif; font-size: 5.5px; line-height: 11.3px;
    margin-top: 5px; width: 400px;
  }
  .value__body--wide { width: 424px; }
  .value__body--mid { width: 380px; }
  .value__body--narrow { width: 356px; }

  .contact { position: absolute; top: 694px; display: flex; align-items: center; gap: 8px;
    font-size: 8.5px; line-height: 13px; }
  .contact__icon { width: 34px; height: 34px; flex: none; }
  .contact--address { left: 35px; }
  .contact--hours { left: 189px; }
  .contact--phone { left: 308px; }
</style>
</head>
<body>

<section class="page page--cover">
  <svg class="page__art" viewBox="0 0 1143 1478" preserveAspectRatio="none">
    <defs>
      <linearGradient id="coverField" x1="0" y1="0" x2="0.4" y2="1">
        <stop offset="0" stop-color="#22380a"/>
        <stop offset="0.55" stop-color="#4a7a1e"/>
        <stop offset="1" stop-color="#77ad38"/>
      </linearGradient>
      <radialGradient id="illustrationTone" cx="0.5" cy="0.45" r="0.6">
        <stop offset="0" stop-color="#173a40"/>
        <stop offset="0.6" stop-color="#0a2630"/>
        <stop offset="1" stop-color="#061d24"/>
      </radialGradient>
    </defs>
    <path d="M140,0 H1143 V1255 C960,1185 770,1030 668,840 L300,210 Z" fill="url(#coverField)"/>
    <path d="M300,210 L668,840 C560,830 420,760 330,640 C240,520 230,330 300,210 Z" fill="#ffffff"/>
    <path d="M208,520 C190,300 330,110 560,52 C780,0 980,110 1030,330 C1080,540 960,760 810,810 C930,720 990,560 960,400 C920,190 740,80 560,100 C360,120 240,300 240,560 Z" fill="var(--green)"/>
    <circle cx="615" cy="470" r="372" fill="var(--green-deep)"/>
    <circle cx="615" cy="460" r="335" fill="url(#illustrationTone)" role="img" aria-label="Illustration of two head silhouettes with line-drawn brains and leafy sprigs"/>
    <polygon points="50,735 235,735 235,915" fill="var(--green)" opacity="0.35" role="img" aria-label="Dotted triangle pattern"/>
    <rect x="832" y="1298" width="136" height="50" fill="var(--green-mid)" opacity="0.35" role="img" aria-label="Zigzag line pattern"/>
  </svg>

  <div class="brand">
    <span class="brand__ring"></span>
    <p class="brand__name">Quellarive<br>Care</p>
  </div>
  <p class="tagline">Discover a better way<br>to a better you</p>
</section>

<section class="page page--values">
  <svg class="page__art" viewBox="0 0 1143 1478" preserveAspectRatio="none">
    <defs>
      <linearGradient id="edgeWave" x1="0" y1="0" x2="1" y2="1">
        <stop offset="0" stop-color="#8cc43f"/>
        <stop offset="1" stop-color="#6aa530"/>
      </linearGradient>
      <linearGradient id="edgeWaveDeep" x1="1" y1="0" x2="0" y2="1">
        <stop offset="0" stop-color="#3f8a3a"/>
        <stop offset="1" stop-color="#8cc43f"/>
      </linearGradient>
      <linearGradient id="rule" x1="0" y1="0" x2="1" y2="0">
        <stop offset="0" stop-color="#7ab03a"/>
        <stop offset="1" stop-color="#1c3008"/>
      </linearGradient>
    </defs>
    <path d="M1143,210 C1090,300 1075,420 1090,520 C1110,640 1050,730 990,850 C930,980 930,1200 1010,1478 H1143 Z" fill="url(#edgeWave)"/>
    <path d="M1143,320 C1100,380 1105,450 1120,500 C1135,550 1143,560 1143,560 Z" fill="url(#edgeWaveDeep)" opacity="0.6"/>
    <path d="M1143,990 C1040,1040 960,1150 965,1300 C968,1380 990,1440 1010,1478 H1143 Z" fill="url(#edgeWaveDeep)" opacity="0.55"/>

    <path d="M0,155 H95 Q135,155 135,198 V1140 Q135,1182 93,1182 H0" fill="none" stroke="var(--green)" stroke-width="6"/>

    <g class="value-markers">
      <g transform="translate(138,253)">
        <circle r="46" fill="#fff" stroke="var(--green-dark)" stroke-width="9"/>
        <path d="M-10,-44 A46,46 0 0 1 44,10" fill="none" stroke="var(--green)" stroke-width="9"/>
        <circle cx="-8" cy="-8" r="11" fill="none" stroke="var(--green-dark)" stroke-width="3"/>
        <circle cx="10" cy="10" r="10" fill="none" stroke="var(--green-dark)" stroke-width="3"/>
      </g>
      <g transform="translate(138,448)">
        <circle r="46" fill="#fff" stroke="var(--green-dark)" stroke-width="9"/>
        <path d="M-10,-44 A46,46 0 0 1 44,10" fill="none" stroke="var(--green)" stroke-width="9"/>
        <circle cx="-10" cy="-16" r="5" fill="none" stroke="var(--green-dark)" stroke-width="3"/>
        <path d="M-18,20 V-6 H-2 V20 M8,-20 C20,-10 4,0 16,10" fill="none" stroke="var(--green-dark)" stroke-width="3"/>
      </g>
      <g transform="translate(138,623)">
        <circle r="46" fill="#fff" stroke="var(--green-dark)" stroke-width="9"/>
        <path d="M-10,-44 A46,46 0 0 1 44,10" fill="none" stroke="var(--green)" stroke-width="9"/>
        <rect x="-18" y="-20" width="26" height="38" rx="3" fill="none" stroke="var(--green-dark)" stroke-width="3"/>
        <circle cx="12" cy="8" r="9" fill="#fff" stroke="var(--green-dark)" stroke-width="3"/>
        <path d="M12,3 V13 M7,8 H17" stroke="var(--green-dark)" stroke-width="3"/>
      </g>
      <g transform="translate(138,840)">
        <circle r="46" fill="#fff" stroke="var(--green-dark)" stroke-width="9"/>
        <path d="M-10,-44 A46,46 0 0 1 44,10" fill="none" stroke="var(--green)" stroke-width="9"/>
        <circle cx="4" cy="-4" r="13" fill="none" stroke="var(--green-dark)" stroke-width="3"/>
        <path d="M-5,5 L-20,20" stroke="var(--green-dark)" stroke-width="4"/>
      </g>
      <g transform="translate(138,1067)">
        <circle r="46" fill="#fff" stroke="var(--green-dark)" stroke-width="9"/>
        <path d="M-10,-44 A46,46 0 0 1 44,10" fill="none" stroke="var(--green)" stroke-width="9"/>
        <circle cx="2" cy="-2" r="11" fill="none" stroke="var(--green-dark)" stroke-width="3"/>
        <path d="M2,-8 V4 M-4,-2 H8 M-20,14 C-8,22 8,22 20,12" fill="none" stroke="var(--green-dark)" stroke-width="3"/>
      </g>
    </g>

    <rect x="0" y="1345" width="878" height="7" rx="3.5" fill="url(#rule)"/>
  </svg>

  <h1 class="values__title">WHAT WE DO</h1>
  <h2 class="values__subtitle">CORE VALUES OF CARE</h2>

  <article class="value" style="top:126px">
    <h3 class="value__heading">An Integrative Approach</h3>
    <p class="value__lead">Join us in our mission to change healthcare as we know it.</p>
    <p class="value__body">Guided step-by-step by our care team, we'll embark on an integrative approach to cover more of the issues we face across the lifespan. Dedicated Attention People are more confused than ever when it comes to their health and they don't know WHO or WHAT to believe. Taking charge of your health requires much more than just your typical 7-minute doctor's visit, which can't even cover the basics of what you need to know to heal. During your in-depth intake consultation, we take the time needed, one-on-one, to thoroughly explore the unique health concerns that keep you from living your best life.</p>
  </article>

  <article class="value" style="top:224px">
    <h3 class="value__heading">Personalized Care</h3>
    <p class="value__lead">This is no “one-size-fits-all” when it comes to giving yourself the best care. Everyone is biologically unique, and as we age, we have different needs and requirements.</p>
    <p class="value__body">First we get to the bottom of your worst symptoms with advanced lab evaluation. After we craft your personalized and targeted healing plan, we also empower you with the knowledge and tools to choose a smarter lifestyle that supports your healing so you don't find yourself right back where you started a year later.</p>
  </article>

  <article class="value" style="top:312px">
    <h3 class="value__heading">Innovative Treatments</h3>
    <p class="value__lead">Did you know that it takes on average 17 years for clinical breakthroughs to make their way into your conventional doctor's office?</p>
    <p class="value__body value__body--wide">That means many health care practitioners are dispensing outdated advice and not using the best evaluation techniques for your particular symptoms and circumstances. Chances are they are not even aware of the proper evaluation that could make all the difference in your healing plan. At Quellarive Care we provide the best of both worlds…traditional approaches in body &amp; mind health with clinicians who also have advanced training in functional medicine – to deliver the best, most advanced evaluation paired with current treatments and nutritional science so that we can look beyond symptoms to provide solutions to your mind and body health concerns.</p>
  </article>

  <article class="value" style="top:422px">
    <h3 class="value__heading">Root Cause Resolution</h3>
    <p class="value__lead">We get to the bottom of WHY you feel sluggish, depressed, anxious, distracted, can't release stubborn weight, or struggle with brain fog.</p>
    <p class="value__body value__body--mid">Traditional outdated healthcare models focus on treating symptoms and ignore the core reason(s) behind why things you have tried aren't working. Our practice uses the tools often found in functional medicine, including a more complete evaluation to see the factors and reasons behind why you are stuck. Many people are struggling with neurotransmitter deficiencies, nutritional deficits, stealth infections, toxicity, potential food intolerances and allergies, and gut &amp; hormonal imbalances that are not traditionally detected by conventional medical evaluation.</p>
  </article>

  <article class="value" style="top:536px">
    <h3 class="value__heading">Co-Creating Health</h3>
    <p class="value__lead">Changing your lifestyle may seem daunting, but we also equip you with mindset tools &amp; mentorship to overcome life habits that are an impediment to optimal wellness.</p>
    <p class="value__body value__body--narrow">We make the prospect of getting healthy “enjoyable.” We have a wide range of tools to support you during your body &amp; mind health transformation and help build resilience and regain energy. We do this through the Whole Balance (WB) Method. We also leverage health coaching and other forms of support &amp; accountability so your new healing lifestyle will become an integral part of your everyday life. We also harness the support of online communities to give you support remotely, as you make important health changes. We serve clients in Harlow, Pinebrook, Ashford, Cedarvale, Milbury, Oak Hollow TN, and surrounding areas.</p>
  </article>

  <div class="contact contact--address">
    <svg class="contact__icon" viewBox="0 0 34 34"><circle cx="17" cy="17" r="16" fill="none" stroke="var(--green)" stroke-width="1.2"/><path d="M17,26 C12,20 11,17 11,14 A6,6 0 0 1 23,14 C23,17 22,20 17,26 Z" fill="none" stroke="var(--green-dark)" stroke-width="1.3"/><circle cx="17" cy="14" r="2.2" fill="none" stroke="var(--green-dark)" stroke-width="1.2"/></svg>
    <p>418 Alder Bend Rd.<br>Harlow, TN 37190</p>
  </div>
  <div class="contact contact--hours">
    <svg class="contact__icon" viewBox="0 0 34 34"><circle cx="17" cy="17" r="16" fill="none" stroke="var(--green)" stroke-width="1.2"/><circle cx="17" cy="17" r="7" fill="none" stroke="var(--green-dark)" stroke-width="1.3"/><path d="M17,13 V17 H20" fill="none" stroke="var(--green-dark)" stroke-width="1.3"/></svg>
    <p>Monday - Friday:<br>8am - 7pm</p>
  </div>
  <div class="contact contact--phone">
    <svg class="contact__icon" viewBox="0 0 34 34"><circle cx="17" cy="17" r="16" fill="none" stroke="var(--green)" stroke-width="1.2"/><path d="M12,10 L15,10 L16,14 L14,15.5 C15,18 16,19 18.5,20 L20,18 L24,19 L24,22 C24,23 23,24 22,24 C16,24 10,18 10,12 C10,11 11,10 12,10 Z" fill="none" stroke="var(--green-dark)" stroke-width="1.2"/><path d="M19,10 A5,5 0 0 1 24,15 M19,13 A2,2 0 0 1 21,15" fill="none" stroke="var(--green-dark)" stroke-width="1.1"/></svg>
    <p>(615) 555 0142</p>
  </div>
</section>

</body>
</html>
```